Psychiatric Office Needs a Website- 1st Time Ever!

Been in practice since 2003 with no website, but finally ready to dive in. We are Maplecrest Behavioral Healthcare, a mental health outpatient practice based in Fayetteville, Georgia that sees diverse individuals and families from childhood to advanced age for a variety of conditions. We've grown by word of mouth and referral but would now like to have a digital footprint. Be the pioneer of our website and we will be sure to share. We would like to see designs that are modern, animated, fairly colorful, easy to read, and caters to all ages. Also, we would like the design to take the whole page (not be centered) and can be viewed well on phone/tablet. Please see our outline for more information. Our motto/slogan is: Maplecrest Behavioral Healthcare- A step forward in your wellness journey, so the design should try to reflect that.
Updates

Project Deadline Extended
Reason: site in progress

Target Market(s)

Children through elderly

Industry/Entity Type

Medical

Logo Text

Stepping forward in your wellness journey

Number of Pages Required

1 page

Colors

Designer to choose colors to be used in the design.

Requirements
Must have
• Animation or moving pictures.
• Color.
• Concise.
• User friendly
• Diversity in the stock photos

```html
<!DOCTYPE html>
<html lang="en">
<head>
<meta charset="utf-8">
<title>Maplecrest Behavioral Healthcare</title>
<link href="https://fonts.googleapis.com/css2?family=Open+Sans:wght@400;600;700&family=Lato:wght@400;700&display=swap" rel="stylesheet">
<style>
:root{
  --brand:#4cbfe9;
  --brand-dark:#3aa9d4;
  --ink:#333;
  --muted:#666;
  --light-bg:#f0f0f0;
  --faq-bg:#e8e8ea;
  --footer-bg:#333335;
  --white:#fff;
}
*{box-sizing:border-box;margin:0;padding:0}
html,body{width:1200px;height:2875px;overflow:hidden}
body{font-family:"Open Sans",Arial,sans-serif;color:var(--ink);background:var(--white);position:relative}
.wrap{position:relative;width:936px;margin:0 auto;height:100%}

/* hero */
.hero{height:645px;position:relative;background:linear-gradient(180deg,#5a6474 0%,#9e9488 30%,#d9b98a 48%,#8c7a66 68%,#3a3330 100%)}
.hero-photo{position:absolute;inset:0;background:radial-gradient(circle at 40% 42%,rgba(255,236,190,.85) 0,rgba(255,220,160,.35) 18%,rgba(0,0,0,0) 45%)}
.brand{position:absolute;left:0;top:20px;display:flex;align-items:center;gap:12px}
.brand-mark{width:150px;height:150px;border-radius:50%;background:var(--brand);border:5px solid var(--white);display:flex;align-items:center;justify-content:center;text-align:center;padding:18px;color:var(--white);font-weight:700;font-size:17px;line-height:1.25}
.topbar{position:absolute;right:0;top:22px;display:flex;gap:26px;font-size:11px;color:var(--white)}
.topbar span{display:flex;align-items:center;gap:6px}
.nav{position:absolute;right:0;top:58px;display:flex;gap:8px}
.nav a{color:var(--white);font-size:11.5px;font-weight:700;text-decoration:none;padding:4px 11px;text-transform:uppercase}
.nav a.active{background:var(--white);color:var(--ink)}
.hero-copy{position:absolute;left:86px;top:210px;width:420px;color:var(--white);font-size:29px;line-height:1.4;font-weight:400}
.btn-screen{position:absolute;left:88px;top:370px;width:205px;height:48px;background:var(--brand);border:2px solid var(--white);color:var(--white);font-weight:700;font-size:15px;display:flex;align-items:center;justify-content:center;letter-spacing:.5px}
.dots{position:absolute;left:0;right:0;display:flex;justify-content:center;gap:9px}
.dots i{width:7px;height:7px;border-radius:50%;background:var(--white)}
.dots i.on{background:var(--brand)}
.dots.grey i{background:#bbb}
.dots.grey i.on{background:var(--brand)}

/* section headings */
.section-title{text-align:center;color:var(--brand);font-size:21px;font-weight:700;padding-top:36px}
.section-title:after{content:"";display:block;width:30px;height:3px;background:var(--brand);margin:14px auto 0}

/* services */
.services{height:624px;background:var(--light-bg)}
.service-grid{display:grid;grid-template-columns:repeat(3,301px);gap:19px 17px;margin-top:38px}
.service-card{height:211px;position:relative;color:var(--white)}
.service-card .label{position:absolute;left:16px;bottom:12px;font-size:12.5px;font-weight:700;text-transform:uppercase;line-height:1.3;width:175px}
.service-card .go{position:absolute;right:12px;bottom:10px;width:20px;height:20px;background:var(--brand);display:flex;align-items:center;justify-content:center}
.ph-a{background:linear-gradient(160deg,#c7d3da,#6f8795 70%,#36454f)}
.ph-b{background:linear-gradient(160deg,#2c3a48,#5b7f9d 55%,#e2b89a)}
.ph-c{background:linear-gradient(160deg,#12263c,#2f5a80 60%,#0d1926)}
.ph-d{background:linear-gradient(160deg,#d9d4cc,#a99b8a 60%,#54483e)}
.ph-e{background:linear-gradient(160deg,#eee9e4,#d8b8a2 55%,#b8403a)}
.ph-f{background:linear-gradient(160deg,#efece7,#c9bfb3 60%,#6d6a68)}
.shade{position:absolute;inset:0;background:linear-gradient(180deg,rgba(0,0,0,0) 55%,rgba(0,0,0,.55))}

/* vision */
.vision{height:422px;background:var(--brand);color:var(--white)}
.vision .wrap{display:flex}
.vision-text{width:516px;padding-top:46px}
.vision-text h2{font-size:21px;font-weight:700}
.vision-text h2:after{content:"";display:block;width:40px;height:2px;background:var(--white);margin-top:12px}
.vision-text h3{font-size:13px;font-weight:700;margin-top:26px}
.vision-text p{font-size:13.5px;line-height:1.45;margin-top:4px}
.vision-text hr{border:0;border-top:1px solid rgba(255,255,255,.45);margin-top:22px;width:496px}
.read-more{display:inline-block;margin-top:28px;background:#444;color:var(--white);font-size:10.5px;font-weight:700;padding:10px 18px;text-transform:uppercase}
.vision-divider{width:1px;background:rgba(255,255,255,.4);margin:50px 0 50px 52px}
.vision-mark{flex:1;display:flex;align-items:center;justify-content:center}
.vision-mark div{width:282px;height:282px;border-radius:50%;background:var(--white)}

/* news */
.news{height:489px;background:var(--white)}
.news-row{display:grid;grid-template-columns:repeat(3,295px);gap:25px;margin-top:44px;position:relative}
.news-card{height:286px;position:relative;color:var(--white)}
.news-card .caption{position:absolute;left:0;right:0;bottom:0;height:92px;background:rgba(40,40,40,.72);padding:12px 18px}
.news-card .date{font-size:9.5px}
.news-card h4{font-size:12px;font-weight:700;margin-top:3px;text-transform:uppercase}
.news-card p{font-size:11.5px;line-height:1.35;margin-top:4px;width:190px;color:#ddd}
.ph-g{background:linear-gradient(160deg,#1c2733,#4b5a6a 50%,#a9b3bb)}
.ph-h{background:linear-gradient(160deg,#dfe6ea,#9fb4b6 50%,#5c6f7d)}
.ph-i{background:linear-gradient(160deg,#eef0f2,#c9a68a 50%,#6a87a8)}
.arrow{position:absolute;top:120px}
.arrow.left{left:-62px}
.arrow.right{right:-62px}

/* faq */
.faq{height:345px;background:var(--faq-bg);position:relative}
.faq-row{display:grid;grid-template-columns:repeat(4,222px);gap:16px;margin-top:46px}
.faq-card{height:131px;background:var(--white);padding:24px 26px}
.faq-card h5{font-size:12px;font-weight:600;line-height:1.35}
.faq-card p{font-size:12px;line-height:1.35;margin-top:12px;color:var(--ink)}
.faq-dots{top:296px}

/* footer */
.footer{height:350px;background:var(--footer-bg);color:var(--white)}
.footer .cols{display:flex;padding-top:50px}
.footer-brand{width:208px}
.footer-brand .brand-mark{width:154px;height:154px;font-size:17px}
.footer h6{font-size:11px;font-weight:700;text-transform:uppercase;margin-bottom:18px}
.contact{width:260px;padding-top:10px}
.contact li{list-style:none;display:flex;gap:14px;font-size:11.5px;line-height:1.5;margin-bottom:14px;color:#ddd}
.menu{width:207px;padding-top:10px}
.menu li{list-style:none;font-size:11.5px;line-height:1.55;color:#ddd}
.newsletter{flex:1;padding-top:10px}
.newsletter .field{height:36px;background:var(--white);color:#333;font-size:11.5px;padding:11px 12px}
.newsletter .signup{display:inline-block;margin-top:14px;background:var(--brand);color:var(--white);font-size:11px;font-weight:700;padding:10px 22px}
.footer-bottom{position:absolute;left:0;right:0;top:256px;border-top:1px solid #555;display:flex;justify-content:space-between;align-items:center;padding-top:22px;font-size:11px}
.follow{display:flex;align-items:center;gap:12px;font-weight:700;text-transform:uppercase}
.follow i{width:28px;height:28px;border-radius:50%;background:#3e66b4;display:block}
</style>
</head>
<body>

<header class="hero">
  <div class="hero-photo" role="img" aria-label="Woman with arms raised in a field at sunset"></div>
  <div class="wrap">
    <div class="brand">
      <div class="brand-mark">Maplecrest Behavioral Healthcare</div>
    </div>
    <div class="topbar">
      <span><svg width="10" height="10" viewBox="0 0 10 10"><circle cx="5" cy="5" r="4" fill="none" stroke="#fff" stroke-width="1.3"/><path d="M5 2.5V5h2" stroke="#fff" stroke-width="1.2" fill="none"/></svg>M-F : 9.00 AM - 9.00PM</span>
      <span><svg width="10" height="10" viewBox="0 0 10 10"><path d="M2 1l2 2-1 1.5c.7 1.2 1.3 1.8 2.5 2.5L7 6l2 2-1.3 1.3C4.5 9 1 5.5.7 2.3z" fill="#fff"/></svg>555.014.2290</span>
      <span><svg width="10" height="10" viewBox="0 0 10 10"><circle cx="5" cy="3" r="2.2" fill="#fff"/><path d="M1 10c0-3 2-4 4-4s4 1 4 4z" fill="#fff"/></svg>PATIENT PORTAL</span>
    </div>
    <nav class="nav">
      <a class="active">Home</a><a>About us</a><a>Services</a><a>Conditions we treat</a><a>New patients</a>
    </nav>
    <h1 class="hero-copy">Maplecrest Behavioral Healthcare- A step forward in your wellness journey</h1>
    <div class="btn-screen">TAKE A SCREENING</div>
  </div>
  <div class="dots" style="top:597px"><i></i><i></i><i class="on"></i><i></i><i></i></div>
</header>

<section class="services">
  <div class="wrap">
    <h2 class="section-title">Our Services</h2>
    <div class="service-grid">
      <div class="service-card ph-a" role="img" aria-label="Clinician with patient in a hospital room"><div class="shade"></div><div class="label">Diagnostic evaluation and treatment</div><span class="go"><svg width="8" height="8" viewBox="0 0 8 8"><path d="M2 1l3 3-3 3" stroke="#fff" stroke-width="1.5" fill="none"/></svg></span></div>
      <div class="service-card ph-b" role="img" aria-label="Brain scans on a tablet"><div class="shade"></div><div class="label">Psychopharmacology</div><span class="go"><svg width="8" height="8" viewBox="0 0 8 8"><path d="M2 1l3 3-3 3" stroke="#fff" stroke-width="1.5" fill="none"/></svg></span></div>
      <div class="service-card ph-c" role="img" aria-label="Surgeon reviewing monitors"><div class="shade"></div><div class="label">Bariatric pre-surgical consultation</div><span class="go"><svg width="8" height="8" viewBox="0 0 8 8"><path d="M2 1l3 3-3 3" stroke="#fff" stroke-width="1.5" fill="none"/></svg></span></div>
      <div class="service-card ph-d" role="img" aria-label="Man in a wheelchair"><div class="shade"></div><div class="label">Disability and work-related reports</div><span class="go"><svg width="8" height="8" viewBox="0 0 8 8"><path d="M2 1l3 3-3 3" stroke="#fff" stroke-width="1.5" fill="none"/></svg></span></div>
      <div class="service-card ph-e" role="img" aria-label="Baby playing with a bead toy"><div class="shade"></div><div class="label">Early childhood assessments</div><span class="go"><svg width="8" height="8" viewBox="0 0 8 8"><path d="M2 1l3 3-3 3" stroke="#fff" stroke-width="1.5" fill="none"/></svg></span></div>
      <div class="service-card ph-f" role="img" aria-label="Man in a counselling session"><div class="shade"></div><div class="label">Substance abuse assessments</div><span class="go"><svg width="8" height="8" viewBox="0 0 8 8"><path d="M2 1l3 3-3 3" stroke="#fff" stroke-width="1.5" fill="none"/></svg></span></div>
    </div>
  </div>
</section>

<section class="vision">
  <div class="wrap">
    <div class="vision-text">
      <h2>Vision &amp; Mission</h2>
      <h3>Vision</h3>
      <p>To be the leading provider of outpatient psychiatric care in Atlanta Metro South, working together to promote (the) mental wellness of our community</p>
      <hr>
      <h3>Mission</h3>
      <p>To provide mental health services to children, adults, and the developmentally disabled population that is culturally sensitive regardless of age, race, gender, orientation, religion, or creed;</p>
      <span class="read-more">Read more</span>
    </div>
    <div class="vision-divider"></div>
    <div class="vision-mark"><div></div></div>
  </div>
</section>

<section class="news">
  <div class="wrap">
    <h2 class="section-title">News &amp; Events</h2>
    <div class="news-row">
      <svg class="arrow left" width="20" height="34" viewBox="0 0 20 34"><path d="M16 3L4 17l12 14" stroke="#aaa" stroke-width="3" fill="none"/></svg>
      <div class="news-card ph-g" role="img" aria-label="Digital brain illustration on a hand"><div class="caption"><div class="date">SEP 20,2017</div><h4>Lorem ipsum is simply dummy</h4><p>There are many variations of pass ages of Lorem</p></div></div>
      <div class="news-card ph-h" role="img" aria-label="Doctor handing over medication"><div class="caption"><div class="date">SEP 20,2017</div><h4>Lorem ipsum is simply dummy</h4><p>There are many variations of pass ages of Lorem</p></div></div>
      <div class="news-card ph-i" role="img" aria-label="Doctor consulting an elderly patient"><div class="caption"><div class="date">SEP 20,2017</div><h4>Lorem ipsum is simply dummy</h4><p>There are many variations of pass ages of Lorem</p></div></div>
      <svg class="arrow right" width="20" height="34" viewBox="0 0 20 34"><path d="M4 3l12 14L4 31" stroke="#aaa" stroke-width="3" fill="none"/></svg>
    </div>
  </div>
</section>

<section class="faq">
  <div class="wrap">
    <h2 class="section-title">FAQ</h2>
    <div class="faq-row">
      <div class="faq-card"><h5>What do I need to bring with me to my first visit?</h5><p>Insurance card, patient forms found on our</p></div>
      <div class="faq-card"><h5>How long do I have to wait to be seen?</h5><p>We try to have very little wait time for your convenience.</p></div>
      <div class="faq-card"><h5>What types of insurance do you accept?</h5><p>We accept a large variety of insurance plans.</p></div>
      <div class="faq-card"><h5>Why is my child not doing well in school?</h5><p>Your child may need some testing</p></div>
    </div>
  </div>
  <div class="dots grey faq-dots"><i></i><i></i><i class="on"></i><i></i><i></i></div>
</section>

<footer class="footer">
  <div class="wrap">
    <div class="cols">
      <div class="footer-brand"><div class="brand-mark">Maplecrest Behavioral Healthcare</div></div>
      <div class="contact">
        <h6>Contact us</h6>
        <ul>
          <li><svg width="10" height="14" viewBox="0 0 10 14"><path d="M5 0a5 5 0 0 1 5 5c0 3.5-5 9-5 9S0 8.5 0 5a5 5 0 0 1 5-5z" fill="#fff"/><circle cx="5" cy="5" r="1.8" fill="#333"/></svg><span>2210 Willow Run Lane<br>Fayetteville, GA 30214</span></li>
          <li><svg width="10" height="10" viewBox="0 0 10 10"><path d="M2 1l2 2-1 1.5c.7 1.2 1.3 1.8 2.5 2.5L7 6l2 2-1.3 1.3C4.5 9 1 5.5.7 2.3z" fill="#fff"/></svg><span>555.014.2290</span></li>
          <li><svg width="12" height="9" viewBox="0 0 12 9"><rect width="12" height="9" fill="#fff"/><path d="M0 0l6 5 6-5" stroke="#333" fill="none"/></svg><span>hello@maplecrestbh.com</span></li>
        </ul>
      </div>
      <div class="menu">
        <h6>Menu</h6>
        <ul><li>Home</li><li>About us</li><li>Services</li><li>Conditions We Treat</li><li>New Patients</li><li>Contact us</li></ul>
      </div>
      <div class="newsletter">
        <h6>Newsletter</h6>
        <div class="field">E mail id</div>
        <span class="signup">SIGNUP</span>
      </div>
    </div>
    <div class="footer-bottom">
      <div class="follow">Follow us on <i></i></div>
      <div>Copyrights @ 2017 All Rights Reserved</div>
    </div>
  </div>
</footer>

</body>
</html>
```